Business Card Design for Online Gift Business

Business card design for a new online Canadian company called "Harlow & Brine Gift Boxes" selling modern and luxurious gift boxes for every occasion. Items are sourced locally from talented socially-responsible Canadian artisans. Each gift is elegantly presented in a keepsake wood box to ensure a lasting impression.

Industry/Entity Type

E-Commerce

Contact Information for Business Card

Marla Whitcombe, Proprietor
Ashbury, AB
403-555-2741
www.harlowandbrine.ca
hello@harlowandbrine.ca

Requirements
Must have
• Crafted with care, given with love
• Please also include the symbols for Facebook and Instagram
Nice to have
• **I have attached a few samples of background colors and font colors that I like. I hope this helps in a few directions to try.

```html
<!DOCTYPE html>
<html lang="en">
<head>
<meta charset="utf-8">
<title>Harlow &amp; Brine Gift Boxes – Business Card</title>
<link href="https://fonts.googleapis.com/css2?family=Carlito:wght@400&family=Cormorant+Garamond:ital,wght@0,500;1,400&display=swap" rel="stylesheet">
<style>
  :root {
    --backdrop: #869a98;
    --card: #060806;
    --gold: #b7a96a;
    --muted: #858e8f;
  }
  * { margin: 0; padding: 0; box-sizing: border-box; }
  html, body { width: 980px; height: 1200px; overflow: hidden; }
  body { background: var(--backdrop); position: relative; font-family: "Carlito", sans-serif; }

  .card { position: absolute; width: 713px; background: var(--card); }
  .card--front { left: 126px; top: 132px; height: 411px; }
  .card--back  { left: 120px; top: 711px; height: 413px; }

  .brand-name {
    position: absolute;
    font-family: "Cormorant Garamond", serif;
    font-weight: 500;
    color: var(--gold);
    white-space: nowrap;
    transform: translate(-50%, -50%);
    letter-spacing: 1px;
  }
  .card--front .brand-name { left: 356px; top: 196px; font-size: 62px; }
  .card--back .brand-name  { left: 186px; top: 214px; font-size: 44px; }

  .tagline {
    position: absolute; left: 342px; top: 308px;
    transform: translate(-50%, -50%);
    font-family: "Cormorant Garamond", serif; font-style: italic;
    font-size: 22px; color: var(--gold); white-space: nowrap;
  }

  .social-list { position: absolute; left: 5px; top: 340px; list-style: none; }
  .social-list li { display: flex; align-items: center; height: 26px; font-size: 14px; color: var(--gold); }
  .social-dot { width: 20px; height: 20px; border-radius: 50%; background: var(--gold); margin-right: 14px; flex: none; }

  .divider { position: absolute; left: 357px; top: 120px; width: 1px; height: 205px; background: var(--gold); opacity: .8; }

  .holder { position: absolute; left: 384px; top: 74px; width: 250px; text-align: center; color: var(--gold); }
  .holder-name { font-size: 32px; line-height: 1.1; text-align: left; white-space: nowrap; }
  .holder-role { font-size: 23px; line-height: 1.1; }

  .contact-list { position: absolute; left: 396px; top: 161px; list-style: none; }
  .contact-list li { display: flex; align-items: center; height: 42px; font-size: 18px; color: var(--muted); letter-spacing: .3px; white-space: nowrap; }
  .contact-icon { width: 28px; height: 28px; margin-right: 26px; flex: none; fill: none; stroke: var(--gold); stroke-width: 1.6; }
  .contact-icon .solid { fill: var(--gold); stroke: none; }
</style>
</head>
<body>

<section class="card card--front" aria-label="Card front">
  <div class="brand-name">Harlow &amp; Brine</div>
  <p class="tagline">Crafted with care, given with love</p>
  <ul class="social-list">
    <li><span class="social-dot"></span>Fernpage.com</li>
    <li><span class="social-dot"></span>Snapgallery.com</li>
  </ul>
</section>

<section class="card card--back" aria-label="Card back">
  <div class="brand-name">Harlow &amp; Brine</div>
  <div class="divider"></div>
  <div class="holder">
    <p class="holder-name">Marla Whitcombe</p>
    <p class="holder-role">Proprietor</p>
  </div>
  <ul class="contact-list">
    <li>
      <svg class="contact-icon" viewBox="0 0 28 28" aria-hidden="true"><path class="solid" d="M7 3l4 1 1 5-3 2c1 3 4 6 7 7l2-3 5 1 1 4c-1 3-3 4-5 4C11 23 5 17 4 8c0-2 1-4 3-5z"/></svg>
      403-555-2741
    </li>
    <li>
      <svg class="contact-icon" viewBox="0 0 28 28" aria-hidden="true"><rect x="4" y="11" width="20" height="14"/><path d="M4 11l10 8 10-8M8 13V3h12v10M11 7h6M11 10h6"/></svg>
      hello@harlowandbrine.ca
    </li>
    <li>
      <svg class="contact-icon" viewBox="0 0 28 28" aria-hidden="true"><circle cx="14" cy="14" r="10"/><ellipse cx="14" cy="14" rx="4.5" ry="10"/><path d="M4 14h20M6 9h16M6 19h16"/></svg>
      www.harlowandbrine.ca
    </li>
    <li>
      <svg class="contact-icon" viewBox="0 0 28 28" aria-hidden="true"><path class="solid" d="M18 2a6 6 0 0 1 6 6c0 4-6 10-6 10s-6-6-6-10a6 6 0 0 1 6-6z"/><circle cx="18" cy="8" r="2" fill="#060806" stroke="none"/><path class="solid" d="M3 20h9l-2 6H1zM14 21h6l2 5h-9z"/></svg>
      Ashbury, AB
    </li>
  </ul>
</section>

</body>
</html>
```